I need a fresh looking, exciting and loaded design for Full service Restaurant

We need a web design for our restaurant, which offers full service Pakistani and Indian food in PA, USA. Design should be elegant, simplified so customers can navigate easily and order food online for catering as well as delivery. We need loads of pictures and room to grow. I already have a web address via vemrilo.com. It should include SSL and e-commerce for ordering food.
Be original and be creative and make it a fun site :)

```html
<!DOCTYPE html>
<html lang="en">
<head>
<meta charset="utf-8">
<title>Saffron Courtyard – Indian &amp; Pakistani Restaurant</title>
<link rel="stylesheet" href="https://fonts.googleapis.com/css2?family=Lobster&family=Open+Sans:wght@400;600;700&display=swap">
<style>
  :root{
    --green:#2f6b14;
    --green-dark:#1d4509;
    --green-deep:#163a07;
    --red:#c8161d;
    --red-dark:#9c0f14;
    --white:#ffffff;
    --text:#8a8a8a;
    --title:#3f7a1a;
    --food-warm:#b8733c;
    --food-deep:#6b3b1c;
  }
  *{margin:0;padding:0;box-sizing:border-box}
  html,body{width:723px;height:1200px;overflow:hidden;background:var(--white)}
  body{position:relative;font-family:"Open Sans",Arial,sans-serif}

  .site-header{position:absolute;top:0;left:0;width:723px;height:58px;background:var(--white);text-align:center}
  .brand{display:inline-flex;align-items:center;gap:8px;margin-top:10px}
  .brand-dot{width:26px;height:26px;border-radius:50%;background:var(--red)}
  .brand-name{font-family:"Lobster",cursive;font-size:22px;color:var(--red);line-height:1}
  .brand-tagline{font-size:7px;color:#666;margin-top:2px;letter-spacing:.3px}

  .main-nav{position:absolute;top:58px;left:0;width:723px;height:36px;background:linear-gradient(var(--green),var(--green-dark))}
  .main-nav ul{list-style:none;display:flex;justify-content:center;gap:30px;height:100%;align-items:center}
  .main-nav a{font-family:"Lobster",cursive;color:var(--white);font-size:17px;text-decoration:none}
  .main-nav .is-active{position:relative;background:var(--red);padding:10px 12px 5px;margin-top:-8px;box-shadow:0 2px 3px rgba(0,0,0,.3)}

  .hero{position:absolute;top:94px;left:0;width:723px;height:347px;background:radial-gradient(ellipse at 50% 55%,#c9824a 0%,#a86a3b 30%,#d8c9ae 65%,#efe6d6 100%)}
  .hero-title{position:absolute;top:150px;width:100%;text-align:center;font-family:"Lobster",cursive;font-size:38px;color:var(--white);text-shadow:0 2px 4px rgba(0,0,0,.5)}
  .hero-arrow{position:absolute;top:160px}
  .hero-arrow.left{left:12px}.hero-arrow.right{right:12px}

  .feature-band{position:absolute;top:441px;left:0;width:723px;height:241px;background:radial-gradient(ellipse at center,var(--green) 0%,var(--green-deep) 100%)}
  .feature-card{position:absolute;top:40px;width:172px}
  .feature-photo{height:118px;border:2px solid var(--white)}
  .feature-btn{height:24px;background:linear-gradient(var(--red),var(--red-dark));color:var(--white);font-family:"Lobster",cursive;font-size:14px;text-align:center;line-height:24px}

  .reviews{position:absolute;top:682px;left:0;width:723px;height:390px}
  .reviews h2{position:absolute;top:22px;width:100%;text-align:center;font-family:"Lobster",cursive;font-weight:400;font-size:24px;color:var(--title)}
  .review{position:absolute;top:72px;width:172px;text-align:center}
  .review-photo{height:106px}
  .review-dish{margin-top:12px;font-size:9px;font-weight:700;color:var(--red);letter-spacing:.3px}
  .review-stars{margin-top:3px;color:var(--red);font-size:9px;letter-spacing:1px}
  .review-text{margin-top:6px;font-size:6.5px;line-height:11px;color:var(--text);padding:0 4px}
  .review-avatar{width:34px;height:34px;border-radius:50%;background:#c9b9a6;margin:8px auto 0;border:2px solid #eee}
  .review-name{margin-top:6px;font-size:8px;color:#555}

  .site-footer{position:absolute;top:1072px;left:0;width:723px;height:128px;background:linear-gradient(var(--green),var(--green-dark));text-align:center;color:var(--white)}
  .social{display:flex;justify-content:center;gap:8px;margin-top:30px}
  .social span{width:10px;height:10px;border-radius:50%;background:var(--white)}
  .footer-links{margin-top:22px;font-size:7px;letter-spacing:.5px}
  .copyright{margin-top:10px;font-size:6.5px;letter-spacing:.5px}
</style>
</head>
<body>

<header class="site-header">
  <div class="brand"><span class="brand-dot"></span><span class="brand-name">Saffron Courtyard</span></div>
  <div class="brand-tagline">A Fine Indian &amp; Pakistani Kitchen</div>
</header>

<nav class="main-nav">
  <ul>
    <li><a class="is-active" href="#">Home</a></li>
    <li><a href="#">About Us</a></li>
    <li><a href="#">Services</a></li>
    <li><a href="#">Menu</a></li>
    <li><a href="#">Location</a></li>
    <li><a href="#">Contact Us</a></li>
  </ul>
</nav>

<section class="hero" role="img" aria-label="Grilled tandoori prawns on a wooden board with spices">
  <svg class="hero-arrow left" width="12" height="20" viewBox="0 0 12 20"><path d="M10 2 2 10l8 8" fill="none" stroke="#fff" stroke-width="2"/></svg>
  <h1 class="hero-title">Saffron Courtyard</h1>
  <svg class="hero-arrow right" width="12" height="20" viewBox="0 0 12 20"><path d="m2 2 8 8-8 8" fill="none" stroke="#fff" stroke-width="2"/></svg>
</section>

<section class="feature-band">
  <div class="feature-card" style="left:87px">
    <div class="feature-photo" role="img" aria-label="Bowls of colourful Indian spices" style="background:linear-gradient(135deg,#c7652a,#8a3d1a,#d9a441)"></div>
    <div class="feature-btn">Saffron Courtyard India</div>
  </div>
  <div class="feature-card" style="left:272px">
    <div class="feature-photo" role="img" aria-label="Plate of Pakistani rice and curry" style="background:linear-gradient(135deg,#e6d6b8,#b78a52,#7d5a32)"></div>
    <div class="feature-btn">Saffron Courtyard Pakistan</div>
  </div>
  <div class="feature-card" style="left:460px">
    <div class="feature-photo" role="img" aria-label="Today's special dish with landmark backdrop" style="background:linear-gradient(135deg,#8fb3c9,#c9b08a,#a0522d)"></div>
    <div class="feature-btn">Todays Special</div>
  </div>
</section>

<section class="reviews">
  <h2>Customer Reviews</h2>
  <article class="review" style="left:87px">
    <div class="review-photo" role="img" aria-label="Chettinad curry in a bowl" style="background:linear-gradient(135deg,#7a3a16,#c8702e,#5a2a10)"></div>
    <div class="review-dish">CHETTINAD CURRY</div>
    <div class="review-stars">★★★★★</div>
    <p class="review-text">Rich, fragrant and perfectly spiced. The sauce was creamy with a gentle heat, and every bite tasted freshly made. Friendly staff and quick service made our dinner truly memorable.</p>
    <div class="review-avatar" role="img" aria-label="Customer portrait"></div>
    <div class="review-name">Daniel Rourke</div>
  </article>
  <article class="review" style="left:272px">
    <div class="review-photo" role="img" aria-label="Mehali kabab served on a plate" style="background:linear-gradient(135deg,#6b4a24,#b8864a,#4a5a2a)"></div>
    <div class="review-dish">MEHALI KABAB</div>
    <div class="review-stars">★★★★★</div>
    <p class="review-text">Rich, fragrant and perfectly spiced. The sauce was creamy with a gentle heat, and every bite tasted freshly made. Friendly staff and quick service made our dinner truly memorable.</p>
    <div class="review-avatar" role="img" aria-label="Customer portrait"></div>
    <div class="review-name">Daniel Rourke</div>
  </article>
  <article class="review" style="left:460px">
    <div class="review-photo" role="img" aria-label="Punjabi curry with bread" style="background:linear-gradient(135deg,#d9c7a8,#b5562a,#5a2e18)"></div>
    <div class="review-dish">PUNJABI</div>
    <div class="review-stars">★★★★★</div>
    <p class="review-text">Rich, fragrant and perfectly spiced. The sauce was creamy with a gentle heat, and every bite tasted freshly made. Friendly staff and quick service made our dinner truly memorable.</p>
    <div class="review-avatar" role="img" aria-label="Customer portrait"></div>
    <div class="review-name">Daniel Rourke</div>
  </article>
</section>

<footer class="site-footer">
  <div class="social"><span></span><span></span><span></span><span></span><span></span></div>
  <div class="footer-links">HOME &nbsp;|&nbsp; ABOUT US &nbsp;|&nbsp; SERVICES &nbsp;|&nbsp; MENU &nbsp;|&nbsp; LOCATION &nbsp;|&nbsp; CONTACT US</div>
  <div class="copyright">© 2016 COMPANY NAME &nbsp;|&nbsp; ALL RIGHTS RESERVED</div>
</footer>

</body>
</html>
```